Business Card For Halvenmoor Financial Consulting

Hi, I would like a business card designed. Bold, modern.
Please use the same design as the logo. I have also attached the website design to see the overall theme.
Wordmark Font
Color: Hex: #01AEF7

```html
<!DOCTYPE html>
<html lang="en">
<head>
<meta charset="utf-8">
<title>Halvenmoor Financial Consulting – Business Card</title>
<link rel="stylesheet" href="https://fonts.googleapis.com/css2?family=Lato:wght@400;700&family=Montserrat:wght@600&display=swap">
<style>
  :root {
    --stage: #2a2a2c;
    --card: #18222c;
    --accent: #01aef7;
    --ink: #ffffff;
    --rule: rgba(255,255,255,0.55);
  }
  * { margin: 0; padding: 0; box-sizing: border-box; }
  html, body { width: 1200px; height: 875px; overflow: hidden; }
  body {
    background: var(--stage);
    font-family: "Lato", Arial, sans-serif;
    display: flex; align-items: center; justify-content: center; gap: 30px;
  }
  .card {
    position: relative;
    width: 560px; height: 320px;
    background: var(--card);
    box-shadow: 0 18px 40px rgba(0,0,0,0.45);
    overflow: hidden;
  }
  .brand-name {
    font-family: "Montserrat", Arial, sans-serif;
    font-weight: 600;
    color: var(--ink);
    line-height: 1.15;
  }

  /* front */
  .card--front { display: flex; align-items: center; justify-content: center; }
  .card--front .brand-name { font-size: 34px; text-align: center; }

  /* back */
  .card--back .brand-name { position: absolute; top: 30px; right: 30px; font-size: 18px; text-align: right; }
  .divider { position: absolute; left: 30px; right: 30px; top: 150px; height: 1px; background: var(--rule); }
  .person { position: absolute; left: 34px; top: 176px; }
  .person__name { font-family: "Montserrat", Arial, sans-serif; font-weight: 600; font-size: 21px; color: var(--ink); text-transform: uppercase; }
  .person__role { font-size: 14px; color: var(--accent); margin-top: 2px; }
  .person__rule { width: 190px; height: 1px; background: var(--rule); margin: 8px 0; }
  .contacts { list-style: none; }
  .contacts li { display: flex; align-items: center; gap: 8px; font-size: 11.5px; color: var(--ink); line-height: 1.55; }
  .contacts svg { width: 10px; height: 10px; fill: var(--accent); flex: none; }
  .office { position: absolute; right: 30px; top: 166px; text-align: right; font-size: 11.5px; color: var(--ink); line-height: 1.5; font-style: normal; }
  .office__company { font-weight: 700; }
  .office__web { color: var(--accent); font-size: 12.5px; margin-top: 4px; }
</style>
</head>
<body>
  <section class="card card--front">
    <p class="brand-name">Halvenmoor<br>Financial Consulting</p>
  </section>

  <section class="card card--back">
    <p class="brand-name">Halvenmoor<br>Financial Consulting</p>
    <div class="divider"></div>

    <div class="person">
      <p class="person__name">Daniel Rowe</p>
      <p class="person__role">Founder &amp; CEO</p>
      <div class="person__rule"></div>
      <ul class="contacts">
        <li><svg viewBox="0 0 10 10"><path d="M2 0h2l1 2.5-1.3 1A5 5 0 0 0 6.5 6.3l1-1.3L10 6v2c0 1-1 2-2 2A8 8 0 0 1 0 2c0-1 1-2 2-2z"/></svg>(555) 201-4470</li>
        <li><svg viewBox="0 0 10 10"><path d="M2.5 0h5a1 1 0 0 1 1 1v8a1 1 0 0 1-1 1h-5a1 1 0 0 1-1-1V1a1 1 0 0 1 1-1zm.5 1.5v6h4v-6z"/></svg>(555) 201-4471</li>
        <li><svg viewBox="0 0 10 10"><path d="M2.5 0h5v3h-5zM0 3.5h10v4H8V10H2V7.5H0zM3 6v3h4V6z"/></svg>(555) 201-4472</li>
        <li><svg viewBox="0 0 10 10"><path d="M0 1.5h10v7H0zM1 2.5l4 3 4-3v-.2H1z"/></svg>info@halvenmoorconsulting.com</li>
      </ul>
    </div>

    <address class="office">
      <p class="office__company">Halvenmoor Consulting Ltd</p>
      <p>Your Address, City</p>
      <p>State, Zip 1235</p>
      <p class="office__web">HalvenmoorConsulting.com</p>
    </address>
  </section>
</body>
</html>
```